I need a business card design for a new business based in South West Australia.
I specialize in residential window cleaning & general handyman maintenance.

Dale Marsh - 412 SILVER HAWK DETAILING
- Window Cleaning
- House Maintenance

```html
<!DOCTYPE html>
<html lang="en">
<head>
<meta charset="utf-8">
<title>412 Silver Hawk Detailing – Business Card</title>
<link rel="stylesheet" href="https://fonts.googleapis.com/css2?family=Arimo:wght@400&family=Libre+Bodoni:wght@700&display=swap">
<style>
  :root {
    --page-bg: #ecebe8;
    --card-white: #ffffff;
    --band-blue: #3d74cf;
    --panel-black: #000000;
    --text-white: #ffffff;
  }
  html, body {
    margin: 0;
    padding: 0;
    width: 1189px;
    height: 1200px;
    overflow: hidden;
    background: var(--page-bg);
  }
  .business-card {
    position: absolute;
    left: 32px;
    top: 278px;
    width: 1125px;
    height: 643px;
    background: var(--card-white);
    box-shadow: 0 4px 14px rgba(0,0,0,0.25);
    overflow: hidden;
  }
  .tools-photo {
    position: absolute;
    left: 0;
    top: 0;
    width: 1125px;
    height: 340px;
    display: block;
  }
  .accent-band {
    position: absolute;
    left: 0;
    top: 340px;
    width: 100%;
    height: 42px;
    background: var(--band-blue);
  }
  .identity-panel {
    position: absolute;
    left: 0;
    top: 382px;
    width: 100%;
    height: 261px;
    background: var(--panel-black);
    color: var(--text-white);
    text-align: center;
  }
  .company-name {
    margin: 0;
    position: absolute;
    top: 40px;
    width: 100%;
    font-family: "Arimo", Arial, sans-serif;
    font-weight: 400;
    font-size: 48px;
    letter-spacing: 0.5px;
    line-height: 1;
  }
  .owner-name {
    margin: 0;
    position: absolute;
    top: 132px;
    width: 100%;
    font-family: "Libre Bodoni", "Bodoni Moda", serif;
    font-weight: 700;
    font-size: 62px;
    line-height: 1;
  }
</style>
</head>
<body>
  <main class="business-card">
    <svg class="tools-photo" role="img" aria-label="Photo of many raised hands holding handyman and painting tools: hoses, tap, paint roller, mallet, scraper, brushes, colour swatches, valves, paint tin and pipe fittings" viewBox="0 0 1125 340" preserveAspectRatio="none">
      <defs>
        <linearGradient id="toolsTones" x1="0" y1="0" x2="1" y2="0">
          <stop offset="0" stop-color="#e7b9a0"/>
          <stop offset="0.2" stop-color="#f0d27a"/>
          <stop offset="0.45" stop-color="#c9a0c8"/>
          <stop offset="0.6" stop-color="#9fd0b8"/>
          <stop offset="0.8" stop-color="#f2c07a"/>
          <stop offset="1" stop-color="#d8b6a2"/>
        </linearGradient>
        <linearGradient id="fadeWhite" x1="0" y1="0" x2="0" y2="1">
          <stop offset="0" stop-color="#ffffff" stop-opacity="0.85"/>
          <stop offset="0.5" stop-color="#ffffff" stop-opacity="0.2"/>
          <stop offset="1" stop-color="#ffffff" stop-opacity="0.55"/>
        </linearGradient>
      </defs>
      <rect width="1125" height="340" fill="url(#toolsTones)"/>
      <rect width="1125" height="340" fill="url(#fadeWhite)"/>
    </svg>
    <div class="accent-band"></div>
    <section class="identity-panel">
      <h1 class="company-name">412 SILVER HAWK DETAILING</h1>
      <p class="owner-name">Dale Marsh</p>
    </section>
  </main>
</body>
</html>
```